Agriculture Business Card

I want to use my existing logo and use my tagline of "Don't Guess...Soil Test" on the card. Looking for a double sided card that will really get peoples attention.
Contact Info:
Marlow Field Crop Edge
Calvin Brusk
2917 K Lane
Larkin, NE 68593
402-555-0193
calvin.r.brusk@fieldmailbox.net

```html
<!DOCTYPE html>
<html lang="en">
<head>
<meta charset="utf-8">
<title>Marlow Field Crop Edge — Business Card</title>
<link href="https://fonts.googleapis.com/css2?family=Fira+Sans+Condensed:wght@600&family=Roboto:wght@400;500&display=swap" rel="stylesheet">
<style>
  :root {
    --soil: #8f5a3f;
    --soil-light: #a5694a;
    --leaf: #5cb33a;
    --harvest: #f7ad1c;
    --paper: #ffffff;
    --ink: #333333;
    --backdrop: #e7e5e2;
  }
  * { margin: 0; padding: 0; box-sizing: border-box; }
  html, body { width: 1200px; height: 900px; overflow: hidden; }
  body {
    background: var(--backdrop);
    font-family: "Roboto", Arial, sans-serif;
    position: relative;
  }
  .card {
    position: absolute;
    left: 270px;
    width: 660px;
    height: 377px;
    border-radius: 24px;
    overflow: hidden;
    box-shadow: 0 8px 24px rgba(0,0,0,0.18);
  }
  .card-front { top: 50px; background: var(--paper); }
  .card-back {
    top: 473px;
    background: linear-gradient(135deg, var(--soil) 0%, var(--soil-light) 100%);
  }
  .front-bands { position: absolute; inset: 0; width: 100%; height: 100%; }

  .brand {
    position: absolute;
    left: 60px;
    top: 92px;
    width: 230px;
    display: flex;
    align-items: center;
    gap: 12px;
  }
  .brand-dot {
    flex: none;
    width: 34px; height: 34px;
    border-radius: 50%;
    background: var(--harvest);
  }
  .brand-name {
    font-family: "Fira Sans Condensed", "Arial Narrow", sans-serif;
    font-weight: 600;
    font-size: 27px;
    line-height: 1.05;
    color: var(--soil);
  }
  .divider {
    position: absolute;
    left: 318px;
    top: 70px;
    width: 1.5px;
    height: 150px;
    background: var(--leaf);
    opacity: 0.7;
  }
  .person {
    position: absolute;
    left: 342px;
    top: 72px;
  }
  .person-name {
    font-size: 27px;
    font-weight: 500;
    letter-spacing: 1px;
    color: var(--soil);
    text-transform: uppercase;
  }
  .person-role {
    font-size: 14px;
    color: var(--ink);
    margin-top: 2px;
  }
  .contact-list {
    list-style: none;
    margin-top: 16px;
    font-size: 14px;
    color: var(--ink);
  }
  .contact-list li {
    display: flex;
    align-items: center;
    gap: 8px;
    line-height: 24px;
  }
  .contact-icon { width: 12px; height: 12px; flex: none; fill: var(--harvest); }

  .back-brand {
    position: absolute;
    left: 0; right: 0;
    top: 130px;
    display: flex;
    justify-content: center;
    align-items: center;
    gap: 14px;
  }
  .back-brand .brand-name { color: var(--harvest); font-size: 34px; }
  .back-brand .brand-dot { width: 40px; height: 40px; background: var(--leaf); }
  .tagline {
    position: absolute;
    left: 0; right: 0;
    top: 220px;
    text-align: center;
    font-size: 24px;
    color: var(--paper);
    letter-spacing: 0.5px;
  }
</style>
</head>
<body>

<section class="card card-front" aria-label="Business card front">
  <svg class="front-bands" viewBox="0 0 660 377" preserveAspectRatio="none" aria-hidden="true">
    <path d="M0 190 C 70 260, 170 330, 300 377 L 0 377 Z" fill="var(--soil)"/>
    <path d="M0 178 C 80 255, 190 330, 320 377" fill="none" stroke="var(--leaf)" stroke-width="6"/>
    <path d="M300 377 L 325 340 C 420 320, 540 300, 660 290 L 660 377 Z" fill="var(--harvest)"/>
  </svg>

  <div class="brand">
    <span class="brand-dot"></span>
    <span class="brand-name">Marlow Field Crop Edge</span>
  </div>

  <div class="divider"></div>

  <div class="person">
    <h1 class="person-name">Calvin Brusk</h1>
    <p class="person-role">CEO/Founder</p>
    <ul class="contact-list">
      <li>
        <svg class="contact-icon" viewBox="0 0 24 24" aria-hidden="true"><path d="M6.6 10.8a15 15 0 0 0 6.6 6.6l2.2-2.2a1 1 0 0 1 1-.25 11.4 11.4 0 0 0 3.6.57 1 1 0 0 1 1 1V20a1 1 0 0 1-1 1A17 17 0 0 1 3 4a1 1 0 0 1 1-1h3.5a1 1 0 0 1 1 1c0 1.25.2 2.45.57 3.57a1 1 0 0 1-.25 1z"/></svg>
        402-555-0193
      </li>
      <li>
        <svg class="contact-icon" viewBox="0 0 24 24" aria-hidden="true"><path d="M2 5h20v14H2z M2 5l10 8 10-8" /></svg>
        calvin.r.brusk@fieldmailbox.net
      </li>
      <li>
        <svg class="contact-icon" viewBox="0 0 24 24" aria-hidden="true"><path d="M12 2a7 7 0 0 0-7 7c0 5.2 7 13 7 13s7-7.8 7-13a7 7 0 0 0-7-7zm0 9.5A2.5 2.5 0 1 1 12 6.5a2.5 2.5 0 0 1 0 5z"/></svg>
        2917 K Lane Larkin, NE 68593
      </li>
    </ul>
  </div>
</section>

<section class="card card-back" aria-label="Business card back">
  <div class="back-brand">
    <span class="brand-dot"></span>
    <span class="brand-name">Marlow Field Crop Edge</span>
  </div>
  <p class="tagline">Don't Guess...Soil Test</p>
</section>

</body>
</html>
```